Business Card for Fashion House

We need a business card design for our personalize fashion service for our customers. the business card should reflect reliability, luxury and creativity.
The brand Gravetto is extracted from "Graceful Velvetto"; Gravetto provides fashion designs sprinkled with luxury and style tailored for our elite clients character profile.
Gravetto is created for those who embody class and elegance with a passion for style.
Target Market(s)
Affluent Customers
Industry/Entity Type
Fashion
Contact Information for Business Card
Samira Haddadin
Fashion Designer
Telephone: +971 4 555 0192
Mobile +971 50 555 0147
Emal info@gravetto-example.com
Website www.gravetto-example.com
Social Media Youtube g+ Facebook Instagram Pin /gravetto
Font styles to use
Other font styles liked:
- Audrey provided
Look and feel
Each slider illustrates characteristics of the customer's brand and the style your logo design should communicate.

```html
<!DOCTYPE html>
<html lang="en">
<head>
<meta charset="utf-8">
<title>Gravetto Business Card</title>
<link rel="stylesheet" href="https://fonts.googleapis.com/css2?family=Marcellus&display=swap">
<style>
  :root {
    --backdrop: #141414;
    --ink: #0b0b0b;
    --paper: #ffffff;
    --paper-shade: #ececec;
    --graphite: #2a2a2a;
    --silver: #d6d6d6;
    --muted: #a9a9a9;
  }
  * { margin: 0; padding: 0; box-sizing: border-box; }
  html, body {
    width: 1200px; height: 864px; overflow: hidden;
    background: var(--backdrop);
    font-family: "Marcellus", "Optima", serif;
  }
  .stage {
    width: 1200px; height: 864px;
    display: flex; align-items: center; justify-content: center; gap: 60px;
  }
  .card {
    position: relative;
    width: 520px; height: 297px;
    overflow: hidden;
    background: var(--ink);
    box-shadow: 0 18px 40px rgba(0,0,0,.6);
  }
  .wordmark {
    color: var(--ink);
    font-size: 26px;
    letter-spacing: 0.42em;
    padding-left: 0.42em;
    text-transform: uppercase;
  }

  /* Front */
  .front__band {
    position: absolute; left: 0; top: 0; width: 100%; height: 160px;
    background: linear-gradient(180deg, var(--paper) 0%, var(--paper-shade) 100%);
    display: flex; align-items: center; justify-content: center;
  }
  .front__details {
    position: absolute; left: 0; top: 160px; width: 100%; height: 137px;
    background: linear-gradient(180deg, var(--ink) 0%, var(--graphite) 100%);
    display: flex; align-items: center;
  }
  .identity {
    width: 205px; text-align: right; padding-right: 16px;
    color: var(--silver);
  }
  .identity__name { font-size: 15px; letter-spacing: 0.04em; }
  .identity__role { font-size: 12px; color: var(--muted); margin-top: 2px; }
  .divider { width: 1px; height: 82px; background: var(--silver); }
  .contacts { list-style: none; padding-left: 16px; color: var(--silver); }
  .contacts li {
    display: flex; align-items: center; gap: 9px;
    font-size: 13px; letter-spacing: 0.05em; line-height: 20px;
  }
  .contacts svg { width: 12px; height: 12px; flex: none; }

  /* Back */
  .back__top { position: absolute; left: 0; top: 0; width: 100%; height: 95px; background: var(--ink); }
  .back__band {
    position: absolute; left: 0; top: 95px; width: 100%; height: 100px;
    background: linear-gradient(180deg, var(--paper) 0%, var(--paper-shade) 100%);
    display: flex; align-items: center; justify-content: center;
  }
  .back__bottom {
    position: absolute; left: 0; top: 195px; width: 100%; height: 102px;
    background: linear-gradient(180deg, var(--graphite) 0%, var(--ink) 100%);
  }
</style>
</head>
<body>
<main class="stage">
  <section class="card card--front" aria-label="Business card front">
    <div class="front__band">
      <span class="wordmark">Gravetto</span>
    </div>
    <div class="front__details">
      <div class="identity">
        <p class="identity__name">Samira Haddadin</p>
        <p class="identity__role">Fashion Designer</p>
      </div>
      <div class="divider"></div>
      <ul class="contacts">
        <li>
          <svg viewBox="0 0 12 12" aria-hidden="true"><circle cx="6" cy="6" r="5.4" fill="none" stroke="currentColor" stroke-width="1"/><path d="M4 3.4h1.2l.5 1.4-.7.5a3.6 3.6 0 0 0 1.7 1.7l.5-.7 1.4.5v1.2c-2.6.3-4.9-2-4.6-4.6z" fill="currentColor"/></svg>
          +971 4 555 0192
        </li>
        <li>
          <svg viewBox="0 0 12 12" aria-hidden="true"><circle cx="6" cy="6" r="5.4" fill="none" stroke="currentColor" stroke-width="1"/><rect x="4.2" y="2.8" width="3.6" height="6.4" rx=".6" fill="none" stroke="currentColor" stroke-width=".9"/></svg>
          +971 50 555 0147
        </li>
        <li>
          <svg viewBox="0 0 12 12" aria-hidden="true"><circle cx="6" cy="6" r="5.4" fill="none" stroke="currentColor" stroke-width="1"/><rect x="3.2" y="4" width="5.6" height="4" fill="none" stroke="currentColor" stroke-width=".9"/><path d="M3.2 4 6 6.2 8.8 4" fill="none" stroke="currentColor" stroke-width=".9"/></svg>
          info@gravetto-example.com
        </li>
        <li>
          <svg viewBox="0 0 12 12" aria-hidden="true"><circle cx="6" cy="6" r="5.4" fill="none" stroke="currentColor" stroke-width="1"/><ellipse cx="6" cy="6" rx="2.2" ry="5.4" fill="none" stroke="currentColor" stroke-width=".8"/><path d="M.6 6h10.8" stroke="currentColor" stroke-width=".8"/></svg>
          www.gravetto-example.com
        </li>
      </ul>
    </div>
  </section>

  <section class="card card--back" aria-label="Business card back">
    <div class="back__top"></div>
    <div class="back__band">
      <span class="wordmark">Gravetto</span>
    </div>
    <div class="back__bottom"></div>
  </section>
</main>
</body>
</html>
```